Business Card & Letterhead Design

We a financial advice company based in Australia. We provide advice to wealthy farmers.

We are changing our business name FROM Brightvale Financial TO Tallowmere Wealth and we need a new letterhead and double sided business card design

Attached is designs from our previous branding (Brightvale Financial) as it includes all the details we require on the new Tallowmere Wealth business cards and letterhead.

Need extra days to review

```html
<!DOCTYPE html>
<html lang="en">
<head>
<meta charset="utf-8">
<title>Tallowmere Wealth Stationery</title>
<link href="https://fonts.googleapis.com/css2?family=Roboto:wght@400;500&family=Roboto+Slab:wght@700&display=swap" rel="stylesheet">
<style>
  :root{
    --backdrop:#9a9a9a;
    --charcoal:#3d3d3d;
    --swoosh:#6f6f6f;
    --paper:#f7f7f5;
    --ink:#3a3a3a;
    --ghost:#ececea;
    --ghost-dark:#474747;
    --light-text:#f2f2f2;
  }
  html,body{margin:0;padding:0;overflow:hidden;}
  body{width:1200px;height:1032px;background:var(--backdrop);position:relative;font-family:'Roboto',sans-serif;}
  .sheet{position:absolute;display:block;}
  .card-front{left:127px;top:330px;width:271px;height:163px;}
  .card-back{left:127px;top:537px;width:271px;height:163px;}
  .letterhead{left:447px;top:74px;width:625px;height:883px;}
  .brand{font-family:'Roboto',sans-serif;font-weight:400;}
  .tagline{font-family:'Roboto',sans-serif;font-weight:400;}
  .contact{font-family:'Roboto',sans-serif;}
  .person{font-family:'Roboto Slab',serif;font-weight:700;}
</style>
</head>
<body>

<svg class="sheet card-front" viewBox="0 0 271 163" aria-label="Business card front">
  <rect width="271" height="163" fill="var(--charcoal)"/>
  <circle class="ghost-ring" cx="225" cy="78" r="88" fill="none" stroke="var(--ghost-dark)" stroke-width="3"/>
  <circle class="brand-ring" cx="135" cy="70" r="21" fill="none" stroke="var(--light-text)" stroke-width="2"/>
  <text class="brand" x="135" y="104" text-anchor="middle" font-size="14.5" fill="var(--light-text)" letter-spacing="0.4">TALLOWMERE WEALTH</text>
  <text class="tagline" x="135" y="114" text-anchor="middle" font-size="6.2" fill="var(--light-text)" letter-spacing="2">STRATEGIC FINANCIAL ADVICE</text>
</svg>

<svg class="sheet card-back" viewBox="0 0 271 163" aria-label="Business card back">
  <rect width="271" height="163" fill="var(--paper)"/>
  <path class="swoosh" d="M60 95 C140 85 220 60 271 2 V18 C220 70 140 92 60 95 Z" fill="var(--swoosh)"/>
  <path class="panel" d="M0 98 C110 98 210 80 271 10 V163 H0 Z" fill="var(--charcoal)"/>
  <circle class="brand-ring" cx="77" cy="33" r="17" fill="none" stroke="var(--ink)" stroke-width="1.8"/>
  <text class="brand" x="77" y="63" text-anchor="middle" font-size="11.5" fill="var(--ink)" letter-spacing="0.3">TALLOWMERE WEALTH</text>
  <text class="tagline" x="77" y="71" text-anchor="middle" font-size="4.8" fill="var(--ink)" letter-spacing="1.5">STRATEGIC FINANCIAL ADVICE</text>

  <g class="contact" fill="var(--light-text)" text-anchor="end">
    <text class="person" x="255" y="71" font-size="9.5">SAM REYES</text>
    <text x="255" y="82" font-size="5.6">B.Ag.Ec. Dip F.P. AFP</text>
    <text x="255" y="90" font-size="5.6">Managing Director</text>
    <text x="243" y="113" font-size="5.8">(07) 3555 0142</text>
    <text x="243" y="122" font-size="5.8">(07) 3555 0187</text>
    <text x="243" y="131" font-size="5.8">0400 555 216</text>
    <text x="243" y="140" font-size="5.8">sam@brightvalefinancial.com.au</text>
    <text x="243" y="149" font-size="5.8">www.brightvalefinancial.com.au</text>
  </g>
  <g class="icons" fill="var(--light-text)">
    <rect x="251" y="108" width="5" height="3.5" rx="1"/>
    <rect x="252" y="116" width="3" height="5" rx="0.6"/>
    <rect x="251" y="126" width="5" height="4" rx="0.6"/>
    <rect x="251" y="135.5" width="5" height="3.5"/>
    <circle cx="253.5" cy="146.5" r="2.5"/>
  </g>
  <g class="contact" fill="var(--light-text)" font-size="5.8">
    <path d="M19 116 a2.6 2.6 0 1 1 5.2 0 c0 2-2.6 4.5-2.6 4.5 s-2.6-2.5-2.6-4.5z"/>
    <path d="M19 139 a2.6 2.6 0 1 1 5.2 0 c0 2-2.6 4.5-2.6 4.5 s-2.6-2.5-2.6-4.5z"/>
    <text x="30" y="121">Suite 8A, 14 Marlow St</text>
    <text x="30" y="130">Riverbend QLD 4102</text>
    <text x="30" y="144">PO Box 4410</text>
    <text x="30" y="153">Eastwood QLD 4102</text>
  </g>
</svg>

<svg class="sheet letterhead" viewBox="0 0 625 883" aria-label="Letterhead">
  <rect width="625" height="883" fill="var(--paper)"/>
  <path class="header-swoosh" d="M46 70 C150 30 260 30 330 55 C420 90 520 128 625 128 V142 C520 142 420 110 330 75 C250 45 150 45 46 70 Z" fill="var(--swoosh)"/>
  <path class="header-band" d="M0 0 H625 V120 C590 124 540 122 480 105 C400 80 330 26 230 14 C150 5 60 20 0 58 Z" fill="var(--charcoal)"/>

  <g class="contact" fill="var(--light-text)" font-size="11" text-anchor="end">
    <text x="579" y="38">(07) 3555 0142</text>
    <text x="579" y="52">(07) 3555 0187</text>
    <text x="579" y="66">0400 555 216</text>
    <text x="579" y="80">sam@brightvalefinancial.com.au</text>
    <text x="579" y="94">brightvalefinancial.com.au</text>
  </g>
  <g class="icons" fill="var(--light-text)">
    <rect x="588" y="31" width="9" height="6" rx="1.5"/>
    <rect x="590" y="43" width="5" height="9" rx="1"/>
    <rect x="588" y="59" width="9" height="7" rx="1"/>
    <rect x="588" y="74" width="9" height="6"/>
    <circle cx="592.5" cy="90" r="4"/>
  </g>

  <circle class="brand-ring" cx="154" cy="121" r="37" fill="none" stroke="var(--ink)" stroke-width="3"/>
  <text class="brand" x="154" y="183" text-anchor="middle" font-size="21" fill="var(--ink)" letter-spacing="0.6">TALLOWMERE WEALTH</text>
  <text class="tagline" x="154" y="196" text-anchor="middle" font-size="8.8" fill="var(--ink)" letter-spacing="2.8">STRATEGIC FINANCIAL ADVICE</text>

  <g class="contact" fill="var(--ink)" font-size="11" text-anchor="end">
    <text x="598" y="176">PO Box 4410 Eastwood QLD 4102</text>
    <text x="598" y="190">Suite 8A, 14 Marlow St Riverbend QLD 4102</text>
  </g>

  <circle class="ghost-ring" cx="314" cy="528" r="196" fill="none" stroke="var(--ghost)" stroke-width="6"/>
</svg>

</body>
</html>
```